Oriel Photography Business Card

I need a business card designed for a photography business based in Perth, Western Australia called Oriel Photography.

We specialise in wedding, event photography and portrait photography.

The business card must borrow the style of the attached logo.

The hex codes for the colours in the logo are:
#ED1D85 - Pink
#89C23E - Green
#37282F - Black

The name on the card will be:
Name: Tobrian
Phone: 0417395268
Website: www.orielphotography.example.com.au
Facebook: orielphotography

I am open and happy to accept creative concepts.

I’d like some space at the back for writing notes and appointment details.

```html
<!DOCTYPE html>
<html lang="en">
<head>
<meta charset="utf-8">
<title>Oriel Photography — Business Card</title>
<link rel="stylesheet" href="https://fonts.googleapis.com/css2?family=Cinzel:wght@500&family=Open+Sans:ital,wght@0,300;0,400;0,600;0,700;1,400&display=swap">
<style>
  :root {
    --pink: #ED1D85;
    --green: #89C23E;
    --ink: #37282F;
    --grey: #5a5a5a;
    --line: #9a9a9a;
    --paper: #ffffff;
    --backdrop: #e9e9ee;
  }
  * { margin: 0; padding: 0; box-sizing: border-box; }
  html, body { width: 1200px; height: 987px; overflow: hidden; }
  body {
    background: var(--backdrop);
    font-family: "Open Sans", Arial, sans-serif;
    color: var(--ink);
    position: relative;
  }
  .card {
    position: absolute;
    left: 280px;
    width: 640px;
    height: 391px;
    background: var(--paper);
    border-radius: 26px;
    overflow: hidden;
    box-shadow: 0 6px 18px rgba(0,0,0,0.12);
  }
  .card--front { top: 62px; }
  .card--back { top: 534px; }

  /* Front */
  .swoosh { position: absolute; inset: 0; }
  .brand {
    position: absolute; left: 170px; top: 54px; width: 400px;
    display: flex; flex-direction: column; align-items: center;
  }
  .brand__mark {
    width: 58px; height: 58px; border-radius: 50%;
    border: 4px solid var(--pink); margin-bottom: 16px;
  }
  .brand__name {
    font-weight: 400; font-size: 15px; letter-spacing: 0.62em;
    text-transform: uppercase; color: var(--ink); white-space: nowrap;
  }
  .person {
    position: absolute; left: 170px; top: 168px; width: 400px; text-align: center;
    font-weight: 700; font-size: 26px; color: var(--pink); letter-spacing: 0.02em;
    text-transform: uppercase;
  }
  .contacts {
    position: absolute; left: 170px; top: 218px; width: 400px;
    display: flex; justify-content: center; gap: 26px; font-size: 17px; color: var(--ink);
  }
  .contact { display: flex; align-items: center; gap: 8px; }
  .contact__icon { width: 18px; height: 18px; flex: none; }
  .contact__square { width: 16px; height: 16px; background: var(--ink); border-radius: 3px; }

  /* Back */
  .appointment__title {
    position: absolute; right: 44px; top: 30px;
    font-family: "Cinzel", Georgia, serif; font-weight: 500;
    font-size: 22px; color: var(--pink); letter-spacing: 0.04em;
  }
  .field {
    position: absolute; left: 52px; display: flex; align-items: flex-end;
    font-size: 15px; color: var(--grey);
  }
  .field__rule { border-bottom: 1px solid var(--line); margin-left: 10px; height: 1px; }
  .field--name { top: 84px; }
  .field--name .field__rule { width: 440px; }
  .field--date { top: 122px; }
  .field--date .field__rule { width: 448px; }
  .field--next { top: 166px; align-items: center; }
  .box {
    display: inline-block; border: 1.5px solid #6e6e6e; border-radius: 3px; background: var(--paper);
  }
  .box--wide { width: 130px; height: 28px; margin: 0 16px 0 10px; }
  .box--day { width: 30px; height: 22px; margin-left: 8px; }
  .ampm { margin-left: 8px; }
  .days {
    position: absolute; left: 52px; top: 226px; display: flex; gap: 22px;
    font-size: 14px; font-weight: 700; color: var(--grey);
  }
  .day { display: flex; align-items: center; }
  .notice {
    position: absolute; left: 52px; top: 282px; font-size: 15px; font-style: italic; color: var(--grey);
  }
  .back-band { position: absolute; left: 0; right: 0; bottom: 0; height: 10px; background: var(--pink); }
  .back-band--green { bottom: 10px; height: 3px; background: var(--green); }
</style>
</head>
<body>

  <section class="card card--front" aria-label="Business card front">
    <svg class="swoosh" width="640" height="391" viewBox="0 0 640 391" aria-hidden="false">
      <path d="M0,186 Q150,318 450,391" fill="none" stroke="var(--green)" stroke-width="7"/>
      <path d="M0,210 Q120,330 420,391 L0,391 Z" fill="var(--pink)"/>
      <text x="18" y="268" transform="rotate(22 18 268)" font-family="Open Sans, Arial, sans-serif"
            font-size="15" fill="#ffffff" letter-spacing="0.5">www.orielphotography.example.com.au</text>
    </svg>

    <div class="brand">
      <span class="brand__mark"></span>
      <span class="brand__name">Oriel Photography</span>
    </div>

    <div class="person">Tobrian</div>

    <div class="contacts">
      <span class="contact">
        <svg class="contact__icon" viewBox="0 0 20 20" aria-hidden="true">
          <circle cx="10" cy="10" r="9" fill="none" stroke="var(--green)" stroke-width="1.6"/>
          <path d="M7 5.5 L8.6 5.5 L9.3 8 L8.2 9 Q9.2 11 11 11.8 L12 10.7 L14.5 11.4 L14.5 13 Q13.5 14.5 11.5 14 Q7 12.5 6 8 Q5.8 6.3 7 5.5 Z" fill="var(--green)"/>
        </svg>
        0417395268
      </span>
      <span class="contact">
        <span class="contact__square"></span>
        orielphotography
      </span>
    </div>
  </section>

  <section class="card card--back" aria-label="Business card back, appointment card">
    <h2 class="appointment__title">YOUR APPOINTMENT</h2>

    <div class="field field--name">Name :<span class="field__rule"></span></div>
    <div class="field field--date">Date :<span class="field__rule"></span></div>
    <div class="field field--next">
      Next Appointment<span class="box box--wide"></span>
      Time :<span class="box box--wide"></span><span class="ampm">am / pm</span>
    </div>

    <div class="days">
      <span class="day">MON<span class="box box--day"></span></span>
      <span class="day">TUE<span class="box box--day"></span></span>
      <span class="day">WED<span class="box box--day"></span></span>
      <span class="day">THU<span class="box box--day"></span></span>
      <span class="day">FRI<span class="box box--day"></span></span>
      <span class="day">SAT<span class="box box--day"></span></span>
    </div>

    <p class="notice">We appreciate a 24 hr. notice for cancellations</p>
  </section>

</body>
</html>
```